Business Cards Needed for Innovative Healthcare Marketing Company

We are a marketing company focused on healthcare. Our company is all about rebranding yourself renewing your image and generating results. The phoenix stands for "reborn" or "rising" which we provide new brands for our clients we take their old brands and renew it with creativity and innovation. I am looking for a business card with color dimension. I have attached an example of a card I think has the look and feel of what I am trying to accomplish. I like that the card example has black and grey font colors, I like the font placement and the small logo, I really like the use of the colors on the right those are the colors of my logo. My logo is phoenix so maybe incorporating flames similar to that design. I would like the back a solid color maybe red with an opaque version of the logo and website. As a marketing company I am always open to creative liberty!

Target Market(s)

Doctors and business professionals.

Industry/Entity Type

Marketing

Contact Information for Business Card

Valcorne Health Care Marketing
Marla Tenwick- CEO
#(512)638-2974
email-marla@valcorne.com
website- valcorne.com

Font styles to use
Sans Serif

Colors
ec1f27
f37122
ffc214
fbed22
fbf289
f04a50

Requirements
Must have
• The logo and required information
Nice to have
• icons by the information
Should not have
• child like font

```html
<!DOCTYPE html>
<html lang="en">
<head>
<meta charset="utf-8">
<title>Valcorne Health Care Marketing — Business Card</title>
<link href="https://fonts.googleapis.com/css2?family=Quicksand:wght@300;400;500&display=swap" rel="stylesheet">
<style>
  :root {
    --red: #ec1f27;
    --deep-red: #c41e24;
    --orange: #f37122;
    --amber: #ffc214;
    --coral: #f04a50;
    --ink: #3a3a3a;
    --grey: #6f6f6f;
    --paper: #ffffff;
    --stage: #ebe7e1;
  }
  * { box-sizing: border-box; margin: 0; padding: 0; }
  html, body {
    width: 780px; height: 1200px; overflow: hidden;
    background: var(--stage);
    font-family: "Quicksand", sans-serif;
  }
  .canvas { position: relative; width: 780px; height: 1200px; }
  .card {
    position: absolute; left: 70px; width: 640px; height: 366px;
    overflow: hidden; border-radius: 4px;
    box-shadow: 0 10px 28px rgba(0,0,0,.18);
  }
  .card--front { top: 150px; background: var(--paper); }
  .card--back  { top: 684px; background: linear-gradient(160deg, #e0262d 0%, var(--deep-red) 100%); }

  .front-shapes { position: absolute; inset: 0; }

  .brand {
    position: absolute; left: 34px; top: 196px;
    display: flex; align-items: center; gap: 8px;
  }
  .brand__dot { width: 30px; height: 30px; border-radius: 50%; background: var(--coral); }
  .brand__name { font-size: 19px; font-weight: 400; color: var(--red); letter-spacing: 1px; line-height: 1; }
  .brand__tag { font-size: 6.5px; color: var(--red); letter-spacing: 1px; margin-top: 3px; }

  .person { position: absolute; left: 250px; top: 198px; }
  .person__name { font-size: 27px; font-weight: 400; color: var(--ink); line-height: 1.1; }
  .person__role { font-size: 14px; color: var(--red); margin-top: 2px; }

  .contacts { list-style: none; margin-top: 14px; }
  .contacts li {
    display: flex; align-items: center; gap: 10px;
    font-size: 14px; color: var(--grey); line-height: 26px;
  }
  .contacts svg { width: 13px; height: 13px; flex: none; }

  .back-mark {
    position: absolute; left: 0; right: 0; top: 118px;
    display: flex; align-items: center; justify-content: center; gap: 18px;
  }
  .back-mark__dot { width: 78px; height: 78px; border-radius: 50%; background: rgba(255,255,255,.16); }
  .back-mark__name { font-size: 58px; font-weight: 300; color: rgba(255,255,255,.38); letter-spacing: 4px; line-height: 1; }
  .back-mark__rule { height: 1px; background: rgba(255,255,255,.35); margin: 10px 0 8px; }
  .back-mark__tag { font-size: 16px; font-weight: 300; color: rgba(255,255,255,.38); letter-spacing: 3px; }
  .back-web { position: absolute; left: 0; right: 0; bottom: 40px; text-align: center; font-size: 14px; color: rgba(255,255,255,.45); letter-spacing: 2px; }
</style>
</head>
<body>
<main class="canvas">

  <section class="card card--front" aria-label="Card front">
    <svg class="front-shapes" viewBox="0 0 640 366" preserveAspectRatio="none" aria-hidden="true">
      <circle cx="600" cy="60" r="250" fill="var(--amber)" opacity=".9"/>
      <circle cx="540" cy="-10" r="200" fill="var(--orange)" opacity=".8"/>
      <circle cx="330" cy="-40" r="200" fill="var(--coral)" opacity=".75"/>
      <circle cx="470" cy="-60" r="150" fill="var(--red)" opacity=".55"/>
      <circle cx="180" cy="-120" r="190" fill="var(--red)" opacity=".35"/>
    </svg>

    <div class="brand">
      <span class="brand__dot"></span>
      <div>
        <div class="brand__name">VALCORNE</div>
        <div class="brand__tag">HEALTHCARE MARKETING</div>
      </div>
    </div>

    <div class="person">
      <h1 class="person__name">Marla Tenwick</h1>
      <p class="person__role">CEO</p>
      <ul class="contacts">
        <li>
          <svg viewBox="0 0 14 14"><rect width="14" height="14" rx="2" fill="var(--red)"/><path d="M4 3.5c.6-.4 1.1-.2 1.4.4l.5 1c.2.4 0 .8-.3 1 .5 1 1.1 1.6 2 2.1.3-.3.7-.4 1-.2l1 .5c.6.3.7.8.3 1.4-.6.8-1.5.9-2.6.3C5.6 9 4.6 7.9 3.8 6.3c-.5-1.1-.4-2.1.2-2.8z" fill="#fff"/></svg>
          (512)638-2974
        </li>
        <li>
          <svg viewBox="0 0 14 14"><rect width="14" height="14" rx="2" fill="var(--red)"/><rect x="3" y="4.5" width="8" height="5.5" fill="#fff"/><path d="M3 4.5l4 3 4-3" stroke="var(--red)" stroke-width=".8" fill="none"/></svg>
          email-marla@valcorne.com
        </li>
        <li>
          <svg viewBox="0 0 14 14"><circle cx="7" cy="7" r="7" fill="var(--red)"/><circle cx="7" cy="7" r="4" fill="none" stroke="#fff" stroke-width=".9"/><path d="M3 7h8M7 3c-1.6 2.4-1.6 5.6 0 8M7 3c1.6 2.4 1.6 5.6 0 8" stroke="#fff" stroke-width=".8" fill="none"/></svg>
          website- valcorne.com
        </li>
      </ul>
    </div>
  </section>

  <section class="card card--back" aria-label="Card back">
    <div class="back-mark">
      <span class="back-mark__dot"></span>
      <div>
        <div class="back-mark__name">VALCORNE</div>
        <div class="back-mark__rule"></div>
        <div class="back-mark__tag">HEALTHCARE MARKETING</div>
      </div>
    </div>
    <p class="back-web">valcorne.com</p>
  </section>

</main>
</body>
</html>
```